BrivoTerna. Lantern of the Steady Harvest. Business card

Professional business card for BrivoTerna (Lantern of the Steady Harvest)
My rationale: Strategy-> Execution-> Results-> Value that lead to the BrivoTerna name: We put the Lantern of the Steady Harvest.
We deliver value to our customers helping them at defining a good strategy (cyan arrow). 90% of well formulated strategies fail due to poor execution so we also consider strategical execution very important (green arrow). Due to the execution we obtain the results (blue arrow). Finally, the results provide feedback to redefine strategy, and the new strategy has to be executed and new results obtained providing new feedback and on and on. It's like a wheel that finally, must create corporate value: value for shareholders, staholders, employees, providers...-

Target Market(s)

CEOs and steering comitees , invewrnent funds

Industry/Entity Type

Business Consultant

Contact Information for Business Card

Teodoro Vinsquel
CEO & Founder
teodoro.vinsquel@brivoterna-example.com
Mobile: +34 655.803.912
www.brivoterna-example.com

Colors

Designer to choose colors to be used in the design.

Requirements
Nice to have
• Nice to hace the words: Strategy, execution, results
• Nice to vave the claim: Lantern of the Steady Harvest
• The three colors should be shown:
• cyan for STRATEGY
• green for EXECUTION
• blue for RESULTS
Should not have
• Complete black background

```html
<!DOCTYPE html>
<html lang="en">
<head>
<meta charset="utf-8">
<title>BrivoTerna – Business Card</title>
<link rel="stylesheet" href="https://fonts.googleapis.com/css2?family=Open+Sans:wght@400;700&display=swap">
<style>
  :root {
    --backdrop: #e8e6e3;
    --card: #ffffff;
    --brand-blue: #123a96;
    --band-blue: #1f3f9e;
    --text-grey: #4a4a4a;
    --rule-grey: #d9d9d9;
  }
  html, body {
    margin: 0;
    padding: 0;
    width: 1200px;
    height: 997px;
    overflow: hidden;
    background: var(--backdrop);
    font-family: "Open Sans", Arial, sans-serif;
  }
  .card {
    position: absolute;
    width: 560px;
    height: 320px;
    background: var(--card);
    box-shadow: 0 8px 24px rgba(0,0,0,0.12);
    overflow: hidden;
  }
  .card--front { left: 80px; top: 110px; }
  .card--back { left: 560px; top: 560px; }

  .brand-name {
    font-weight: 700;
    color: var(--brand-blue);
    letter-spacing: -0.5px;
    margin: 0;
  }
  .card--front .brand-name {
    position: absolute;
    left: 34px;
    top: 150px;
    font-size: 36px;
  }
  .divider {
    position: absolute;
    left: 262px;
    top: 34px;
    width: 1px;
    height: 110px;
    background: var(--rule-grey);
  }
  .contact {
    position: absolute;
    left: 282px;
    top: 32px;
  }
  .contact__name {
    margin: 0;
    font-size: 19px;
    font-weight: 700;
    color: var(--brand-blue);
    line-height: 1.1;
  }
  .contact__role {
    margin: 2px 0 12px;
    font-size: 13px;
    color: var(--text-grey);
  }
  .contact__list {
    list-style: none;
    margin: 0;
    padding: 0;
    font-size: 12px;
    color: var(--text-grey);
  }
  .contact__list li {
    display: flex;
    align-items: center;
    gap: 7px;
    line-height: 19px;
  }
  .contact__list svg { width: 11px; height: 11px; fill: var(--brand-blue); flex: none; }

  .tagline-band {
    position: absolute;
    right: 0;
    top: 196px;
    width: 250px;
    height: 40px;
    background: var(--band-blue);
  }
  .tagline-band__text {
    position: absolute;
    right: 16px;
    top: 0;
    line-height: 40px;
    font-size: 13px;
    color: #ffffff;
    word-spacing: 3px;
  }

  .card--back .brand-name {
    position: absolute;
    left: 0;
    right: 0;
    top: 126px;
    text-align: center;
    font-size: 54px;
  }
</style>
</head>
<body>

<section class="card card--front" aria-label="Business card front">
  <p class="brand-name">BrivoTerna</p>
  <div class="divider"></div>
  <div class="contact">
    <h1 class="contact__name">Teodoro Vinsquel</h1>
    <p class="contact__role">CEO &amp; Founder</p>
    <ul class="contact__list">
      <li>
        <svg viewBox="0 0 12 12" aria-hidden="true"><path d="M3 0h6a1 1 0 0 1 1 1v10a1 1 0 0 1-1 1H3a1 1 0 0 1-1-1V1a1 1 0 0 1 1-1zm0 1.5v8h6v-8z"/></svg>
        +34 655.803.912
      </li>
      <li>
        <svg viewBox="0 0 12 12" aria-hidden="true"><path d="M0 2h12v8H0zm1 1v.4l5 3.2 5-3.2V3z"/></svg>
        teodoro.vinsquel@brivoterna-example.com
      </li>
      <li>
        <svg viewBox="0 0 12 12" aria-hidden="true"><circle cx="6" cy="6" r="6"/><path d="M1 6h10M6 0.5v11" stroke="#fff" stroke-width="0.9"/></svg>
        www.brivoterna-example.com
      </li>
    </ul>
  </div>
  <div class="tagline-band">
    <span class="tagline-band__text">Results - Execution - Strategy</span>
  </div>
</section>

<section class="card card--back" aria-label="Business card back">
  <p class="brand-name">BrivoTerna</p>
</section>

</body>
</html>
```